Business card design for my company.
I would like the card's background colour to be black. You can also see our web site to get an idea of our brand. https://www.tmwhomecrafting.com.au/
- Name
- Email

```html
<!DOCTYPE html>
<html lang="en">
<head>
<meta charset="utf-8">
<title>TMW Home Crafting – Business Card</title>
<link href="https://fonts.googleapis.com/css2?family=Montserrat:wght@300;400;700&display=swap" rel="stylesheet">
<style>
  :root {
    --canvas: #3a3a3a;
    --card: #212121;
    --green: #16a047;
    --white: #f5f6f7;
    --muted: #e6e6e6;
  }
  * { box-sizing: border-box; margin: 0; padding: 0; }
  html, body {
    width: 1200px;
    height: 1200px;
    overflow: hidden;
    background: var(--canvas);
    font-family: "Montserrat", Arial, sans-serif;
  }
  .sheet {
    width: 1200px;
    height: 1200px;
    display: flex;
    align-items: center;
    justify-content: center;
    gap: 70px;
  }
  .card {
    width: 470px;
    height: 750px;
    background: var(--card);
    border-radius: 26px;
    position: relative;
    display: flex;
    flex-direction: column;
    align-items: center;
    color: var(--white);
  }
  .brand {
    display: flex;
    align-items: center;
    gap: 14px;
  }
  .brand-mark {
    width: 22px;
    height: 22px;
    background: var(--green);
  }
  .brand-name {
    font-weight: 700;
    font-size: 30px;
    letter-spacing: 2px;
    color: var(--white);
    line-height: 1.15;
    text-transform: uppercase;
  }
  .card-front .brand { margin-top: 170px; }
  .card-back { justify-content: center; }
  .holder {
    margin-top: 190px;
    text-align: center;
  }
  .holder-name {
    font-weight: 700;
    font-size: 34px;
    letter-spacing: 1.5px;
    color: var(--green);
    text-transform: uppercase;
  }
  .holder-role {
    font-weight: 300;
    font-size: 21px;
    color: var(--white);
    margin-top: 4px;
  }
  .divider {
    width: 14px;
    height: 2px;
    background: var(--green);
    margin: 26px auto 22px;
  }
  .contacts {
    list-style: none;
    display: flex;
    flex-direction: column;
    align-items: center;
    gap: 12px;
  }
  .contact {
    display: flex;
    align-items: center;
    gap: 10px;
    font-size: 19px;
    font-weight: 400;
    color: var(--muted);
  }
  .contact svg { width: 16px; height: 16px; flex: none; }
</style>
</head>
<body>
<main class="sheet">
  <section class="card card-front">
    <div class="brand">
      <span class="brand-mark"></span>
      <span class="brand-name">TMW<br>Home Crafting</span>
    </div>
    <div class="holder">
      <h1 class="holder-name">Declan Hart</h1>
      <p class="holder-role">CEO/Founder</p>
      <div class="divider"></div>
      <ul class="contacts">
        <li class="contact">
          <svg viewBox="0 0 16 16" aria-hidden="true"><path fill="#16a047" d="M4 1.5l2.2 2.6-1.2 1.6c.8 1.9 2.3 3.4 4.3 4.3l1.6-1.2 2.6 2.2-1.4 2.3C7 13 3 9 1.7 3z"/></svg>
          555-201-7749
        </li>
        <li class="contact">
          <svg viewBox="0 0 16 16" aria-hidden="true"><rect x="1" y="3" width="14" height="10" fill="#16a047"/><path d="M1 3.5l7 5 7-5" fill="none" stroke="#212121" stroke-width="1.3"/></svg>
          info@tmwhomecrafting.com.au
        </li>
        <li class="contact">
          <svg viewBox="0 0 16 16" aria-hidden="true"><g fill="none" stroke="#16a047" stroke-width="1.3"><circle cx="8" cy="8" r="6.5"/><ellipse cx="8" cy="8" rx="3" ry="6.5"/><path d="M1.5 8h13M2.5 4.8h11M2.5 11.2h11"/></g></svg>
          www.tmwhomecrafting.com.au
        </li>
      </ul>
    </div>
  </section>

  <section class="card card-back">
    <div class="brand">
      <span class="brand-mark"></span>
      <span class="brand-name">TMW<br>Home Crafting</span>
    </div>
  </section>
</main>
</body>
</html>
```